Create a memorable Stationary for Security Software Company

Velbrantix is the worldwide leader in securing the Internet. Making Internet communications and critical data secure, reliable and available everywhere has been and continues to be our ongoing vision. We are committed to staying focused on real customer needs and to developing new and innovative security solutions that redefine the security landscape.

Industry/Entity Type

Internet

Font styles to use
Serif
Sans Serif
Script

Colors
0792cd
33a6d7
85cae6

```html
<!DOCTYPE html>
<html lang="en">
<head>
<meta charset="utf-8">
<title>Velbrantix Business Card</title>
<link href="https://fonts.googleapis.com/css2?family=Open+Sans:wght@400;600;700&display=swap" rel="stylesheet">
<style>
  :root {
    --blue-deep: #0792cd;
    --blue-mid: #33a6d7;
    --blue-light: #85cae6;
    --ink: #2b2b2b;
    --paper: #ffffff;
    --backdrop: #ecebe8;
    --edge: #3a3a3a;
  }
  * { margin: 0; padding: 0; box-sizing: border-box; }
  html, body { width: 1200px; height: 1118px; overflow: hidden; }
  body {
    background: var(--backdrop);
    font-family: "Open Sans", Arial, sans-serif;
    color: var(--ink);
    position: relative;
  }
  .card {
    position: absolute;
    width: 819px;
    height: 466px;
    background: var(--paper);
    border: 1.5px solid var(--edge);
    border-radius: 38px;
    overflow: hidden;
  }
  .card--front { left: 346px; top: 54px; }
  .card--back { left: 68px; top: 594px; }

  .swoosh { position: absolute; left: 0; top: 0; width: 819px; height: 300px; }

  .holder { position: absolute; right: 51px; top: 22px; text-align: right; color: #fff; }
  .holder__name { font-size: 32px; font-weight: 700; line-height: 42px; }
  .holder__title { font-size: 27px; font-weight: 400; line-height: 36px; letter-spacing: 0.04em; }

  .brand {
    position: absolute;
    display: flex;
    align-items: center;
    gap: 14px;
    color: var(--blue-mid);
    font-weight: 600;
    font-size: 56px;
    line-height: 1;
    transform: translate(-50%, -50%);
    white-space: nowrap;
  }
  .brand__dot { width: 40px; height: 40px; border-radius: 50%; background: var(--blue-mid); }
  .card--front .brand { left: 210px; top: 210px; }
  .card--back .brand { left: 50%; top: 215px; font-size: 62px; }

  .address { position: absolute; left: 35px; top: 384px; font-size: 19.5px; line-height: 28px; }

  .contacts { position: absolute; right: 51px; top: 303px; list-style: none; font-size: 19.5px; }
  .contacts li { display: flex; justify-content: flex-end; align-items: center; gap: 9px; height: 36.5px; }
  .contacts svg { width: 18px; height: 18px; fill: var(--blue-deep); }

  .back-url {
    position: absolute;
    left: 0; right: 0; top: 356px;
    text-align: center;
    font-size: 25px;
    letter-spacing: 0.3em;
  }
</style>
</head>
<body>
  <section class="card card--front">
    <svg class="swoosh" viewBox="0 0 819 300" aria-hidden="true">
      <path d="M0,0 H819 V292 C600,165 260,42 0,84 Z" fill="var(--blue-mid)"/>
      <path d="M0,0 H819 V262 C600,142 260,32 0,70 Z" fill="#ffffff"/>
      <path d="M0,0 H819 V242 C600,126 260,20 0,62 Z" fill="var(--blue-deep)"/>
    </svg>
    <div class="holder">
      <div class="holder__name">Your Name</div>
      <div class="holder__title">Title</div>
    </div>
    <div class="brand"><span class="brand__dot"></span>Velbrantix</div>
    <div class="address">Street Name, City Name<br>Zipcode-012345</div>
    <ul class="contacts">
      <li><svg viewBox="0 0 24 24"><path d="M6.6 10.8a15 15 0 0 0 6.6 6.6l2.2-2.2c.3-.3.7-.4 1-.2 1.1.4 2.3.6 3.6.6.6 0 1 .4 1 1V20c0 .6-.4 1-1 1A17 17 0 0 1 3 4c0-.6.4-1 1-1h3.5c.6 0 1 .4 1 1 0 1.3.2 2.5.6 3.6.1.3 0 .7-.2 1z"/></svg>012-345-6789</li>
      <li><svg viewBox="0 0 24 24"><path d="M7 1h10a2 2 0 0 1 2 2v18a2 2 0 0 1-2 2H7a2 2 0 0 1-2-2V3a2 2 0 0 1 2-2zm0 3v12h10V4zm5 14a1.5 1.5 0 1 0 0 3 1.5 1.5 0 0 0 0-3z"/></svg>012-345-6789</li>
      <li><svg viewBox="0 0 24 24"><path d="M2 9l10-6 10 6v11H2zm2 1.5V18h16v-7.5l-8 5z"/></svg>info@velbrantix.com</li>
      <li><svg viewBox="0 0 24 24"><path d="M12 2a10 10 0 1 0 0 20 10 10 0 0 0 0-20zm1 2.1c1.2.9 2.2 2.9 2.5 5.9H13zm-2 0V10H8.5c.3-3 1.3-5 2.5-5.9zM4.1 10a8 8 0 0 1 4-5.3C7.2 6 6.6 7.9 6.5 10zm0 2h2.4c.1 2.1.7 4 1.6 5.3a8 8 0 0 1-4-5.3zm4.4 0H11v5.9c-1.2-.9-2.2-2.9-2.5-5.9zm4.5 0h2.5c-.3 3-1.3 5-2.5 5.9zm4.5 0h2.4a8 8 0 0 1-4 5.3c.9-1.3 1.5-3.2 1.6-5.3zm0-2c-.1-2.1-.7-4-1.6-5.3a8 8 0 0 1 4 5.3z"/></svg>www.velbrantix.com</li>
    </ul>
  </section>

  <section class="card card--back">
    <div class="brand"><span class="brand__dot"></span>Velbrantix</div>
    <div class="back-url">www.velbrantix.com</div>
  </section>
</body>
</html>
```